Build Website for Playful Brand that helps content creators build businesses

Please help me create a website for my company that helps content creators build businesses around their audience. I have attached a design and vibe that I am going for at mossquay.io.

Open for changes, but I want to keep the colour I currently have (a light teal). Ultimately the brand is playful but should come off as a very modern elevated brand.

I am looking for a few pages including

1. Home (with clear CTA button)
A section where I can input what the company does, and some brands that we have launched

2. About Me
A simple page, that has preferably able to put a circular image of myself and then give a quick background about the company

3. Blog (can you include how blog posts will appear and it should sit nicely in the page)
This ideally is a section that will be able to link to another software so my blogs automatically flow into here or posts. But otherwise it should have sections of blocks where creators can see about topics that I post about

4. Contact (this should include a form that will allow users to contact me)
Finally a contact page where it links my socials, similar what is there, but ideally there is a form they can fill out which I can link to my inbox as well. This should be a simple page as well

Create a multi page website, including a page that will link or can link blog post

Similar to this vibe and logo - https://mossquay.io/

Target Market(s)

Content Creators

Coding

Coded - Design and coding required

Number of Pages Required

4 page

Requirements
Must have
• Home, Contact Me (Including a place to submit an enquiry and form), Blog Post Page As well

```html
<!DOCTYPE html>
<html lang="en">
<head>
<meta charset="utf-8">
<title>Moss Quay — Home</title>
<link href="https://fonts.googleapis.com/css2?family=Montserrat:ital,wght@0,400;0,500;0,600;0,700;1,400&family=Poppins:wght@400;500;600;700&display=swap" rel="stylesheet">
<style>
:root{
  --teal:#9ad8cf;
  --teal-dark:#2f5f5a;
  --teal-text:#8fd3ca;
  --ink:#1d1d1d;
  --body:#4a4a4a;
  --sky:#bfe6ef;
  --soft:#f6f6f6;
  --white:#fff;
  --sand:#d9c3ae;
  --denim:#8fa9c8;
  --skin:#e8c2a6;
  --stone:#b8b2ac;
}
*{box-sizing:border-box;margin:0;padding:0}
html,body{width:1200px;height:3879px;overflow:hidden}
body{font-family:"Montserrat",sans-serif;color:var(--body);background:var(--white);position:relative}
.abs{position:absolute}
.heading{font-family:"Poppins",sans-serif;font-weight:500;color:var(--ink);font-size:33px;letter-spacing:.5px;text-align:center}
.heading span{color:var(--teal-text);font-weight:600}
.pill{display:flex;align-items:center;justify-content:center;background:var(--teal);color:var(--teal-dark);font-weight:700;font-size:15px;border-radius:24px;letter-spacing:.3px}

/* header */
.topbar{left:0;top:0;width:1200px;height:72px;background:var(--teal)}
.contact-item{top:16px;display:flex;gap:14px;align-items:flex-start}
.contact-item b{display:block;color:var(--white);font-size:14px;font-weight:700}
.contact-item small{display:block;color:var(--white);font-size:13px;margin-top:4px}
.top-btn{top:17px;height:38px;border-radius:20px;font-size:13px;font-weight:700;display:flex;align-items:center;justify-content:center;color:var(--teal-dark)}
.btn-demo{left:793px;width:154px;background:var(--white)}
.btn-free{left:958px;width:156px;border:2px solid var(--teal-dark)}
.nav{top:72px;left:0;width:1200px;height:54px;background:var(--white)}
.nav a{position:absolute;top:18px;font-size:14px;color:var(--ink);text-decoration:none}
.nav .active{left:110px;top:0;width:75px;height:54px;background:#d9f0ec;display:flex;align-items:center;justify-content:center}
.logo-badge{left:500px;top:-52px;width:200px;height:200px;border-radius:50%;background:var(--white);border:3px solid var(--teal);display:flex;flex-direction:column;align-items:center;justify-content:flex-end;padding-bottom:36px;gap:10px;z-index:2}
.logo-dot{width:46px;height:46px;border-radius:50%;background:var(--teal);display:block}
.logo-name{font-size:20px;letter-spacing:3px;color:var(--teal-dark);font-weight:400}

/* hero */
.hero{left:0;top:126px;width:1200px;height:618px;
  background:
    linear-gradient(90deg,#fff 0%,rgba(255,255,255,.96) 22%,rgba(255,255,255,.55) 38%,rgba(255,255,255,0) 52%),
    radial-gradient(ellipse 160px 120px at 610px 170px,rgba(232,205,170,.9),transparent 70%),
    radial-gradient(ellipse 140px 130px at 760px 220px,rgba(205,120,80,.75),transparent 70%),
    radial-gradient(ellipse 200px 200px at 720px 430px,rgba(143,169,200,.9),transparent 70%),
    radial-gradient(ellipse 150px 150px at 1020px 230px,rgba(110,80,60,.7),transparent 70%),
    radial-gradient(ellipse 240px 200px at 1010px 470px,rgba(250,250,250,.95),transparent 70%),
    radial-gradient(ellipse 180px 120px at 700px 560px,rgba(240,238,232,.95),transparent 70%),
    linear-gradient(180deg,#d6d8d4 0%,#cfc6bb 50%,#d9d2c8 100%)}
.hero-copy{left:110px;top:300px}
.hero-copy h2{font-family:"Poppins",sans-serif;font-weight:500;font-size:27px;color:var(--ink)}
.hero-copy h1{font-family:"Poppins",sans-serif;font-weight:700;font-size:42px;color:var(--teal-text);letter-spacing:1px;margin-top:4px}
.hero-copy p{font-size:16.5px;line-height:31px;color:var(--ink);width:420px;margin-top:14px}
.hero-cta{left:110px;top:521px;width:160px;height:44px}

/* about */
.about-photo{left:173px;top:809px;width:352px;height:352px;border-radius:50%;border:6px solid var(--teal);
  background:
    radial-gradient(ellipse 80px 60px at 120px 120px,#2b2b2b,transparent 70%),
    radial-gradient(ellipse 130px 90px at 170px 100px,#555,transparent 70%),
    radial-gradient(ellipse 90px 70px at 150px 170px,rgba(232,194,166,.9),transparent 70%),
    radial-gradient(ellipse 70px 110px at 210px 260px,#fafafa,transparent 70%),
    radial-gradient(circle 30px at 45px 140px,#1e1e1e,transparent 80%),
    radial-gradient(ellipse 30px 60px at 310px 180px,#222,transparent 80%),
    linear-gradient(160deg,#efefef,#dcdcdc 60%,#cfcfcf)}
.about-copy{left:599px;top:836px;width:500px}
.about-copy .heading{text-align:left}
.about-copy p{font-size:16px;line-height:31px;margin-top:18px}
.about-btn{left:599px;top:1078px;width:160px;height:44px}

/* services */
.services-bg{left:0;top:1229px;width:1200px;height:502px;
  background:
    radial-gradient(ellipse 300px 160px at 330px 230px,rgba(215,215,215,.8),transparent 70%),
    radial-gradient(ellipse 260px 180px at 1000px 120px,rgba(225,225,225,.8),transparent 70%),
    linear-gradient(180deg,#ececec,#f2f2f2 70%,#f5f5f5)}
.card{width:227px;background:var(--white);border-radius:6px;box-shadow:0 4px 18px rgba(0,0,0,.08);display:flex;flex-direction:column;align-items:center;text-align:center;padding:26px 10px 0}
.card .icon{width:69px;height:69px;border-radius:50%;background:var(--teal);display:flex;align-items:center;justify-content:center}
.card h3{font-size:18px;font-weight:700;color:var(--ink);line-height:25px;margin-top:20px}
.card p{font-size:14px;line-height:26px;color:var(--body);margin-top:12px}
.card .more{font-size:14px;font-weight:700;color:#444;margin-top:14px;display:flex;gap:8px;align-items:center}
.card.featured{background:var(--teal)}
.card.featured .icon{background:var(--white)}
.card.featured h3,.card.featured .more{color:var(--teal-dark)}
.card.featured p{color:#3d6864}

/* brands */
.brands{left:0;top:2045px;width:1200px;height:418px;background:var(--soft)}
.brand-tile{top:2188px;width:233px;height:111px;background:var(--white);border:1px solid #e6e6e6;border-radius:4px;display:flex;align-items:center;justify-content:center;gap:10px;font-size:15px;font-weight:600;color:#333;letter-spacing:1px}
.brand-tile i{width:22px;height:22px;background:#c9c9c9;display:block}

/* contact */
.contact-photo{left:530px;top:2463px;width:670px;height:497px;
  background:
    radial-gradient(ellipse 200px 140px at 250px 320px,rgba(232,194,166,.85),transparent 70%),
    radial-gradient(ellipse 180px 120px at 430px 380px,rgba(250,250,250,.95),transparent 70%),
    radial-gradient(ellipse 160px 200px at 480px 140px,rgba(250,248,245,.95),transparent 70%),
    radial-gradient(ellipse 140px 160px at 620px 200px,rgba(150,110,80,.6),transparent 70%),
    linear-gradient(120deg,#bda58c,#e2d8cc 40%,#efebe6 70%,#b9a58f)}
.contact-left{left:0;top:2463px;width:660px;height:497px;background:var(--sky);clip-path:polygon(0 0,100% 0,80% 100%,0 100%)}
.form-panel{left:110px;top:2560px;width:546px;height:356px;background:var(--teal)}
.field{background:var(--white);border-radius:17px;height:33px;font-size:11px;color:#999;padding:10px 24px}
.field.box{border-radius:4px;height:67px}
.send{left:155px;top:2826px;width:455px;height:41px;background:var(--white);border-radius:3px;display:flex;align-items:center;justify-content:center;font-weight:700;font-size:15px;color:var(--teal-dark)}

/* reviews */
.review{top:3108px;width:345px;height:174px;border:1px solid #e5e5e5;background:var(--white);box-shadow:0 3px 10px rgba(0,0,0,.05);padding:30px 12px 0 33px;font-style:italic;font-size:13.5px;line-height:23px;color:#333}
.reviewer{top:3312px;display:flex;gap:14px;align-items:center}
.avatar{width:54px;height:54px;border-radius:50%;background:linear-gradient(#a8b4bd,#5c6670);display:block}
.reviewer b{display:block;font-size:18px;font-weight:500;color:#333}
.reviewer em{display:block;font-size:13.5px;color:#333;margin-top:2px}
.dots{left:533px;top:3406px;display:flex;gap:6px}
.dots i{display:block;width:29px;height:6px;border-radius:3px;background:#8a9095}
.dots i.on{background:#2f4a5a}

/* footer */
.footer{left:0;top:3478px;width:1200px;height:401px;background:var(--teal)}
.footer-logo{left:112px;top:3566px;display:flex;flex-direction:column;align-items:center;gap:18px}
.footer-logo i{width:74px;height:74px;border-radius:50%;background:var(--white);display:block}
.footer-logo span{font-size:28px;color:var(--white);letter-spacing:3px}
.fcol{top:3536px}
.fcol h4{font-family:"Poppins",sans-serif;font-size:20px;font-weight:600;color:#3d6864;letter-spacing:.5px}
.fcol a{display:block;font-size:15px;color:#3d6864;text-decoration:none;margin-top:15px;line-height:20.5px}
.fcol a:first-of-type{margin-top:25px}
.social{display:flex;gap:22px;margin-top:44px}
.social i{display:block;width:33px;height:33px;border-radius:50%;background:#2f4a5a}
.rule{left:112px;top:3813px;width:978px;height:1px;background:#3d6864}
.copy{left:0;top:3836px;width:1200px;text-align:center;font-size:13.5px;color:#3d6864}
</style>
</head>
<body>

<header>
  <div class="abs topbar"></div>
  <div class="abs contact-item" style="left:110px">
    <svg width="28" height="28" viewBox="0 0 24 24" fill="none" stroke="#fff" stroke-width="1.4"><path d="M5 3h4l2 5-2.5 1.5a11 11 0 0 0 6 6L16 13l5 2v4a2 2 0 0 1-2 2A16 16 0 0 1 3 5a2 2 0 0 1 2-2z"/></svg>
    <div><b>CALL</b><small>+1(555) 010 2040</small></div>
  </div>
  <div class="abs contact-item" style="left:298px">
    <svg width="34" height="28" viewBox="0 0 28 24" fill="none" stroke="#fff" stroke-width="1.4"><rect x="2" y="4" width="20" height="14" rx="1"/><path d="M2 5l10 7 10-7"/><circle cx="22" cy="17" r="4"/></svg>
    <div><b>E-MAIL</b><small>hello@mossquay.io</small></div>
  </div>
  <div class="abs top-btn btn-demo">REQUEST A DEMO</div>
  <div class="abs top-btn btn-free">START FOR FREE</div>
  <nav class="abs nav">
    <a class="active">Home</a>
    <a style="left:210px">About Us</a>
    <a style="left:315px">Our services</a>
    <a style="left:817px">Our Blog</a>
    <a style="left:918px">FAQ</a>
    <a style="left:987px">Contact Us</a>
  </nav>
  <div class="abs logo-badge"><i class="logo-dot"></i><span class="logo-name">MOSS QUAY</span></div>
</header>

<section>
  <div class="abs hero" role="img" aria-label="Photo of three women working together at a table with a tablet and notebook"></div>
  <div class="abs hero-copy">
    <h2>WELCOME TO</h2>
    <h1>MOSS QUAY</h1>
    <p>Lorem ipsum dolor sit amet, consectetur adipiscing elit, sed do eiusmod tempor incididunt ut labore et dolore magna aliqua.</p>
  </div>
  <div class="abs pill hero-cta">GET STARTED</div>
</section>

<section>
  <div class="abs about-photo" role="img" aria-label="Photo of hands typing on a laptop beside a notebook and coffee cup"></div>
  <div class="abs about-copy">
    <h2 class="heading">ABOUT <span>US</span></h2>
    <p>Lorem ipsum dolor sit amet, consectetur adipiscing elit, sed do eiusmod tempor incididunt ut labore et dolore magna aliqua. Ut enim ad minim veniam, quis nostrud exercitation ullamco laboris nisi ut aliquip ex ea commodo consequat. Duis aute irure dolor in reprehenderit in voluptate.</p>
  </div>
  <div class="abs pill about-btn">READ MORE</div>
</section>

<section>
  <div class="abs services-bg" role="img" aria-label="Faded photo of a desk with laptop and notebook"></div>
  <h2 class="abs heading" style="left:0;top:1306px;width:1200px">OUR <span>SERVICES</span></h2>

  <div class="abs card" style="left:110px;top:1506px;height:353px">
    <div class="icon"><svg width="36" height="36" viewBox="0 0 24 24" fill="none" stroke="#2f5f5a" stroke-width="1.3"><path d="M4 20h16M6 17l9-9 3 3-9 9H6z"/></svg></div>
    <h3>STRATEGIC<br>CONTENT CREATION</h3>
    <p>Lorem ipsum dolor sit amet, consectetur adipiscing elit, sed do eiusmod tempor incididunt ut labore et dolore magna aliqua.</p>
    <div class="more">READ MORE <span>»</span></div>
  </div>
  <div class="abs card" style="left:361px;top:1426px;height:355px">
    <div class="icon"><svg width="36" height="36" viewBox="0 0 24 24" fill="none" stroke="#2f5f5a" stroke-width="1.3"><circle cx="7" cy="6" r="2.5"/><circle cx="17" cy="6" r="2.5"/><path d="M8 12v4a4 4 0 0 0 8 0v-4"/></svg></div>
    <h3>LEAD<br>NURTURING</h3>
    <p>Lorem ipsum dolor sit amet, consectetur adipiscing elit, sed do eiusmod tempor incididunt ut labore et dolore magna aliqua.</p>
    <div class="more">READ MORE <span>»</span></div>
  </div>
  <div class="abs card featured" style="left:613px;top:1506px;height:353px">
    <div class="icon"><svg width="36" height="36" viewBox="0 0 24 24" fill="none" stroke="#2f5f5a" stroke-width="1.3"><circle cx="6" cy="5" r="2"/><circle cx="12" cy="5" r="2"/><circle cx="18" cy="5" r="2"/><path d="M4 10h16M6 13v7M12 13v7M18 13v7M4 18l2 2 2-2M16 18l2 2 2-2"/></svg></div>
    <h3>SEAMLESS<br>CONVERSION</h3>
    <p>Lorem ipsum dolor sit amet, consectetur adipiscing elit, sed do eiusmod tempor incididunt ut labore et dolore magna aliqua.</p>
    <div class="more">READ MORE <span>»</span></div>
  </div>
  <div class="abs card" style="left:864px;top:1426px;height:355px">
    <div class="icon"><svg width="36" height="36" viewBox="0 0 24 24" fill="none" stroke="#2f5f5a" stroke-width="1.3"><circle cx="12" cy="12" r="3"/><circle cx="12" cy="3" r="1.5"/><circle cx="12" cy="21" r="1.5"/><circle cx="3" cy="12" r="1.5"/><circle cx="21" cy="12" r="1.5"/><path d="M12 4.5V9M12 15v4.5M4.5 12H9M15 12h4.5"/></svg></div>
    <h3>COMMUNITY<br>BUILDING</h3>
    <p>Lorem ipsum dolor sit amet, consectetur adipiscing elit, sed do eiusmod tempor incididunt ut labore et dolore magna aliqua.</p>
    <div class="more">READ MORE <span>»</span></div>
  </div>
  <div class="abs pill" style="left:486px;top:1939px;width:228px;height:44px">VIEW ALL SERVICES</div>
</section>

<section>
  <div class="abs brands"></div>
  <h2 class="abs heading" style="left:0;top:2106px;width:1200px">OUR <span>BRANDS</span></h2>
  <div class="abs brand-tile" style="left:106px"><i></i>INKWELL PRESS</div>
  <div class="abs brand-tile" style="left:357px">FENNEL TABLE</div>
  <div class="abs brand-tile" style="left:609px"><i style="border-radius:50%"></i>NORTHGATE CO</div>
  <div class="abs brand-tile" style="left:860px">VELORA</div>
  <div class="abs pill" style="left:486px;top:2343px;width:228px;height:43px">VIEW ALL PARTNERS</div>
</section>

<section>
  <div class="abs contact-photo" role="img" aria-label="Photo of a hand writing in a notebook beside a cup"></div>
  <div class="abs contact-left"></div>
  <h2 class="abs heading" style="left:110px;top:2500px;width:546px">CONTACT <b style="font-weight:700">US</b></h2>
  <div class="abs form-panel"></div>
  <div class="abs field" style="left:155px;top:2611px;width:223px">First Name</div>
  <div class="abs field" style="left:388px;top:2611px;width:222px">Last Name</div>
  <div class="abs field" style="left:155px;top:2671px;width:223px">Phone Number</div>
  <div class="abs field" style="left:388px;top:2671px;width:222px">E-mail</div>
  <div class="abs field box" style="left:155px;top:2730px;width:455px">Message</div>
  <div class="abs send">SEND YOUR MESSAGE</div>
</section>

<section>
  <h2 class="abs heading" style="left:0;top:3021px;width:1200px">CLIENT <span>REVIEWS</span></h2>
  <div class="abs review" style="left:65px">Lorem ipsum dolor sit amet, consectetur adipiscing elit, sed do eiusmod tempor aliqua. Ut enim ad minim veniam,quis nostrud exercitation ullamco laboris nisi ut aliquip ex ea commodo consequat.</div>
  <div class="abs review" style="left:428px">Lorem ipsum dolor sit amet, consectetur adipiscing elit, sed do eiusmod tempor aliqua. Ut enim ad minim veniam,quis nostrud exercitation ullamco laboris nisi ut aliquip ex ea commodo consequat.</div>
  <div class="abs review" style="left:790px">Lorem ipsum dolor sit amet, consectetur adipiscing elit, sed do eiusmod tempor aliqua. Ut enim ad minim veniam,quis nostrud exercitation ullamco laboris nisi ut aliquip ex ea commodo consequat.</div>
  <div class="abs reviewer" style="left:67px"><i class="avatar" role="img" aria-label="Client portrait"></i><div><b>Theo Marsh</b><em>Lorem ipsum dolor sit amet</em></div></div>
  <div class="abs reviewer" style="left:428px"><i class="avatar" role="img" aria-label="Client portrait"></i><div><b>Theo Marsh</b><em>Lorem ipsum dolor sit amet</em></div></div>
  <div class="abs reviewer" style="left:790px"><i class="avatar" role="img" aria-label="Client portrait"></i><div><b>Theo Marsh</b><em>Lorem ipsum dolor sit amet</em></div></div>
  <div class="abs dots"><i></i><i class="on"></i><i></i><i></i></div>
</section>

<footer>
  <div class="abs footer"></div>
  <div class="abs footer-logo"><i></i><span>MOSS QUAY</span></div>
  <div class="abs fcol" style="left:408px"><h4>ABOUT INFO</h4><a>Home</a><a>About</a><a>Services</a><a>Our Blog</a><a>FAQ</a><a>Contact Us</a></div>
  <div class="abs fcol" style="left:657px"><h4>QUICK LINKS</h4><a>Privacy</a><a>Terms of Use</a><a>Cookie preferences</a><a>Site Map</a><a>Contact Us</a><a>Support</a></div>
  <div class="abs fcol" style="left:912px"><h4>QUICK LINKS</h4><div class="social"><i aria-label="Social profile"></i><i aria-label="Social profile"></i></div></div>
  <div class="abs rule"></div>
  <div class="abs copy">Copyright © 2024 mossquay &nbsp;|&nbsp; Privacy Policy &nbsp;|&nbsp; Terms and Conditions.</div>
</footer>

</body>
</html>
```